Spiritual Healing bussiness needs logo/business card

Simple, clean looking logo/card
For spiritual business with healing services and occult rituals

Contact Information for Business Card

Needs my name: Tobin Varley
Business name: Lantern Healing Shop
Services provided and worded in this way:

Reiki Healing
Tarot
Oils
Rituals Of Change

Can look occult like but with light energy.

Colors
0255a3
3276b5
85abd2
33a6d7
85cae6
0292cd

```html
<!DOCTYPE html>
<html lang="en">
<head>
<meta charset="utf-8">
<title>Lantern Healing Shop – Business Card</title>
<link href="https://fonts.googleapis.com/css2?family=Oswald:wght@500&family=Lato:wght@400&display=swap" rel="stylesheet">
<style>
  :root {
    --stage: #232323;
    --card-front: #ffffff;
    --card-back: #0292cd;
    --navy: #0255a3;
    --sky: #33a6d7;
    --ink: #333333;
    --muted: #5a5a5a;
    --white: #ffffff;
  }
  html, body {
    margin: 0;
    width: 1200px;
    height: 900px;
    overflow: hidden;
    background: var(--stage);
  }
  .canvas {
    position: relative;
    width: 1200px;
    height: 900px;
  }
  .card {
    position: absolute;
    top: 200px;
    width: 310px;
    height: 502px;
    box-shadow: 3px 4px 8px rgba(0,0,0,0.55);
    font-family: "Lato", sans-serif;
  }
  .card--front {
    left: 253px;
    background: var(--card-front);
    border-radius: 62px 0 62px 0;
  }
  .card--back {
    left: 627px;
    background: var(--card-back);
    border-radius: 0 62px 0 62px;
  }
  .brand-ring {
    position: absolute;
    border-radius: 50%;
    box-sizing: border-box;
  }
  .card--front .brand-ring {
    left: 93px; top: 76px;
    width: 124px; height: 124px;
    border: 8px solid var(--navy);
  }
  .brand-name {
    position: absolute;
    left: 0; right: 0;
    top: 212px;
    margin: 0;
    text-align: center;
    font-family: "Oswald", sans-serif;
    font-weight: 500;
    font-size: 27px;
    line-height: 1;
    color: var(--navy);
    letter-spacing: 0.2px;
  }
  .tagline {
    position: absolute;
    left: 0; right: 0;
    top: 252px;
    margin: 0;
    text-align: center;
    font-size: 12px;
    color: var(--muted);
    letter-spacing: 0.3px;
  }
  .person-name {
    position: absolute;
    left: 32px;
    top: 348px;
    margin: 0;
    font-family: "Oswald", sans-serif;
    font-weight: 500;
    font-size: 22px;
    line-height: 1;
    color: var(--navy);
  }
  .contact-list {
    position: absolute;
    left: 33px;
    top: 402px;
    margin: 0;
    padding: 0;
    list-style: none;
  }
  .contact-list li {
    display: flex;
    align-items: center;
    gap: 3px;
    height: 19.5px;
    font-size: 14.5px;
    color: var(--ink);
  }
  .contact-icon {
    width: 16px;
    height: 16px;
    flex: none;
  }
  .card--back .brand-ring {
    left: 73px; top: 166px;
    width: 164px; height: 164px;
    border: 12px solid var(--white);
    display: flex;
    align-items: center;
    justify-content: center;
  }
  .brand-name--mark {
    position: static;
    color: var(--white);
    font-size: 21px;
    line-height: 1.15;
  }
  .services {
    position: absolute;
    left: 0; right: 0;
    top: 400px;
    margin: 0;
    padding: 0;
    list-style: none;
    text-align: center;
    color: var(--white);
    font-size: 14.5px;
    line-height: 21px;
    letter-spacing: 0.2px;
  }
  .services .dot {
    display: inline-block;
    width: 7px; height: 7px;
    border-radius: 50%;
    background: var(--white);
    margin: 0 7px;
    vertical-align: 2px;
  }
</style>
</head>
<body>
<main class="canvas">
  <section class="card card--front">
    <div class="brand-ring" aria-hidden="true"></div>
    <h1 class="brand-name">LANTERN HEALING SHOP</h1>
    <p class="tagline">HEALING SERVICES &amp; OCCULT RITUALS</p>
    <h2 class="person-name">TOBIN VARLEY</h2>
    <ul class="contact-list">
      <li>
        <svg class="contact-icon" viewBox="0 0 16 16" aria-hidden="true">
          <circle cx="8" cy="8" r="7.3" fill="none" stroke="#0255a3" stroke-width="1.2"/>
          <path d="M4 6.2c0-1 1.8-1.8 4-1.8s4 .8 4 1.8v.8h-2.2v-1H6.2v1H4z M5 8h6l.8 3.6H4.2z" fill="#0255a3"/>
        </svg>
        044-555 218 640
      </li>
      <li>
        <svg class="contact-icon" viewBox="0 0 16 16" aria-hidden="true">
          <circle cx="8" cy="8" r="7.3" fill="none" stroke="#0255a3" stroke-width="1.2"/>
          <rect x="3.8" y="5" width="8.4" height="6" fill="#0255a3"/>
          <path d="M3.8 5l4.2 3.4L12.2 5" fill="none" stroke="#fff" stroke-width="0.9"/>
        </svg>
        hello@lanternhealing.com
      </li>
      <li>
        <svg class="contact-icon" viewBox="0 0 16 16" aria-hidden="true">
          <circle cx="8" cy="8" r="7.3" fill="none" stroke="#0255a3" stroke-width="1.2"/>
          <circle cx="8" cy="8" r="4.6" fill="#0255a3"/>
          <path d="M3.4 8h9.2M8 3.4c-1.6 1.4-1.6 7.8 0 9.2M8 3.4c1.6 1.4 1.6 7.8 0 9.2" fill="none" stroke="#fff" stroke-width="0.7"/>
        </svg>
        www.LanternHealingShop.com
      </li>
    </ul>
  </section>

  <section class="card card--back">
    <div class="brand-ring">
      <p class="brand-name brand-name--mark">LANTERN<br>HEALING<br>SHOP</p>
    </div>
    <ul class="services">
      <li>REIKI HEALING</li>
      <li>TAROT<span class="dot"></span>OILS</li>
      <li>RITUALS OF CHANGE</li>
    </ul>
  </section>
</main>
</body>
</html>
```